Corvane Capital Business Cards

These are professional business cards that are for my family office.
Put fake emails and phone numbers as of now until I finalize those components. This family office controls my families investments, assets, and future. The cards should be professional.
..
.
.
.
I just uploaded another variation of a logo I would like to see as a business card to I am inbeteen which logo to use

Target Market(s)

business

Industry/Entity Type

business

Contact Information for Business Card

Professional, wealth related, finance related.

Requirements
Must have
• Logo

```html
<!DOCTYPE html>
<html lang="en">
<head>
<meta charset="utf-8">
<title>Corvane Capital Business Cards</title>
<link rel="stylesheet" href="https://fonts.googleapis.com/css2?family=Playfair+Display:wght@400;700&family=Tinos:wght@400;700&display=swap">
<style>
  :root {
    --backdrop: #ececec;
    --gold: #c7ae70;
    --ink: #0a0a0a;
    --paper: #ffffff;
  }
  * { margin: 0; padding: 0; box-sizing: border-box; }
  html, body {
    width: 1200px;
    height: 716px;
    overflow: hidden;
    background: var(--backdrop);
  }
  .canvas {
    position: relative;
    width: 1200px;
    height: 716px;
  }
  .card {
    position: absolute;
    left: 369px;
    width: 461px;
    height: 264px;
    overflow: hidden;
  }
  /* Front */
  .card--front {
    top: 94px;
    background: var(--gold);
  }
  .brand-mark {
    position: absolute;
    left: 216px;
    top: 176px;
    width: 29px;
    height: 29px;
    background: var(--paper);
  }
  .card--front .brand-mark { left: 216px; top: 78px; }
  .front-wordmark {
    position: absolute;
    left: 0;
    right: 0;
    top: 146px;
    text-align: center;
    font-family: "Playfair Display", serif;
    font-weight: 400;
    font-size: 33px;
    letter-spacing: 1px;
    color: var(--paper);
    line-height: 1;
  }
  /* Back */
  .card--back {
    top: 385px;
    background: var(--paper);
  }
  .back-brand {
    position: absolute;
    left: 28px;
    top: 72px;
    width: 190px;
    display: flex;
    align-items: center;
    gap: 10px;
  }
  .back-brand .brand-square {
    flex: none;
    width: 18px;
    height: 18px;
    background: var(--gold);
  }
  .back-brand .brand-name {
    font-family: "Playfair Display", serif;
    font-weight: 400;
    font-size: 25px;
    line-height: 1.1;
    color: var(--ink);
  }
  .divider {
    position: absolute;
    left: 231px;
    top: 73px;
    width: 2px;
    height: 106px;
    background: var(--gold);
  }
  .contact-block {
    position: absolute;
    left: 248px;
    top: 71px;
    font-family: "Tinos", serif;
    color: var(--ink);
  }
  .person-name {
    font-weight: 700;
    font-size: 19px;
    line-height: 1;
  }
  .person-name .surname { color: var(--gold); }
  .person-role {
    margin-top: 4px;
    font-size: 14px;
    line-height: 1;
  }
  .accent-dash {
    margin-top: 8px;
    width: 16px;
    height: 4px;
    background: var(--gold);
  }
  .contact-list {
    list-style: none;
    margin-top: 22px;
  }
  .contact-item {
    display: flex;
    align-items: center;
    gap: 5px;
    font-size: 14px;
    line-height: 19px;
  }
  .contact-item svg { flex: none; width: 12px; height: 10px; fill: var(--gold); }
  .footer-band {
    position: absolute;
    left: 0;
    bottom: 0;
    width: 461px;
    height: 18px;
  }
  .footer-band .band-gold { fill: var(--gold); }
  .footer-band .band-ink { fill: var(--ink); }
</style>
</head>
<body>
<main class="canvas">
  <section class="card card--front" aria-label="Card front">
    <div class="brand-mark"></div>
    <h1 class="front-wordmark">CORVANE CAPITAL</h1>
  </section>

  <section class="card card--back" aria-label="Card back">
    <div class="back-brand">
      <span class="brand-square"></span>
      <span class="brand-name">Corvane Capital</span>
    </div>
    <div class="divider"></div>
    <div class="contact-block">
      <p class="person-name">Elliot <span class="surname">Brandt</span></p>
      <p class="person-role">Founder</p>
      <div class="accent-dash"></div>
      <ul class="contact-list">
        <li class="contact-item">
          <svg viewBox="0 0 12 10" aria-hidden="true"><path d="M1 3.5C1 1.5 3 1 6 1s5 .5 5 2.5v1H8.5V3.2h-5v1.3H1zM3 4.5h6l2 2.5V9H1V7z"/></svg>
          <span>555-014-2768</span>
        </li>
        <li class="contact-item">
          <svg viewBox="0 0 12 10" aria-hidden="true"><path d="M0 1h12v1L6 6 0 2zM0 3.2l6 4 6-4V9H0z"/></svg>
          <span>info@corvaneoffice.com</span>
        </li>
      </ul>
    </div>
    <svg class="footer-band" viewBox="0 0 461 18" aria-hidden="true">
      <polygon class="band-gold" points="0,0 234,0 216,18 0,18"/>
      <polygon class="band-ink" points="240,0 461,0 461,18 222,18"/>
    </svg>
  </section>
</main>
</body>
</html>
```